Pellham Grove Trust - New Website Designed

I need a site that looks like this http://www.quorlandgiving.org for boat donations. So please replace the cars with boats.

```html
<!DOCTYPE html>
<html lang="en">
<head>
<meta charset="utf-8">
<title>Pellham Grove Trust</title>
<link href="https://fonts.googleapis.com/css2?family=Montserrat:wght@400;500;600&family=Open+Sans:wght@400;600&family=Roboto+Slab:wght@400&display=swap" rel="stylesheet">
<style>
:root{
  --blue:#1a4fa0;
  --blue-dark:#163f82;
  --red:#c21a1a;
  --red-dark:#a81414;
  --ink:#333;
  --muted:#777;
  --grey-band:#f3f4f6;
  --panel:#3a3a3a;
  --white:#fff;
}
*{box-sizing:border-box;margin:0;padding:0}
html,body{width:1200px;height:2459px;overflow:hidden;background:var(--white)}
body{position:relative;font-family:"Open Sans",Arial,sans-serif;color:var(--ink)}
.abs{position:absolute}
.brand{left:87px;top:24px;display:flex;align-items:center;gap:12px}
.brand-mark{width:36px;height:36px;border-radius:50%;background:var(--blue)}
.brand-name{font-family:"Montserrat",sans-serif;font-weight:600;font-size:24px;color:var(--blue);text-transform:uppercase}
.tollfree{left:876px;top:16px;display:flex;align-items:center;gap:16px}
.tollfree .ring{width:46px;height:46px;border:2px solid var(--blue);border-radius:50%;display:flex;align-items:center;justify-content:center}
.tollfree small{display:block;font-family:"Montserrat",sans-serif;font-size:16px;color:var(--blue);font-weight:500}
.tollfree strong{display:block;font-family:"Montserrat",sans-serif;font-size:25px;color:var(--blue-dark);font-weight:500}
.nav{left:0;top:87px;width:1200px;height:53px;background:var(--blue)}
.nav ul{list-style:none;display:flex;position:absolute;left:126px;top:0;height:53px;align-items:center}
.nav li{font-family:"Montserrat",sans-serif;font-size:13px;color:var(--white);margin-right:45px;font-weight:500}
.donate-tab{left:803px;top:87px;width:310px;height:53px;background:var(--red);color:var(--white);font-family:"Montserrat",sans-serif;font-size:20px;display:flex;align-items:center;justify-content:center}
.hero{left:0;top:140px;width:1200px;height:473px;background:linear-gradient(90deg,#7a8a4a 0%,#b99a7a 30%,#8a7a5a 55%,#b7424a 80%,#d8d0e4 100%)}
.donate-form{left:803px;top:140px;width:310px;height:437px;background:rgba(58,58,58,.9);padding:26px 20px 0}
.field{height:38px;background:var(--white);border-radius:3px;font-size:12px;color:var(--muted);padding:0 12px;display:flex;align-items:center;justify-content:space-between;margin-bottom:6px}
.row{display:flex;gap:6px}.row .field{flex:1}
.btn-donate{margin:20px auto 0;width:162px;height:40px;background:var(--red);color:var(--white);font-family:"Montserrat",sans-serif;font-size:15px;display:flex;align-items:center;justify-content:center;border-radius:2px}
.dots{left:88px;top:583px;display:flex;gap:5px}
.dots i{width:12px;height:12px;border:2px solid var(--white);border-radius:50%}
.benefits{left:0;top:613px;width:1200px;height:210px;background:linear-gradient(180deg,var(--red),var(--red-dark));display:flex;justify-content:center}
.benefit{width:206px;text-align:center;color:var(--white);font-family:"Montserrat",sans-serif;font-size:16px;line-height:23px;padding-top:36px}
.benefit svg{display:block;margin:0 auto 14px}
.section-title{font-family:"Montserrat",sans-serif;font-size:24px;color:var(--blue);text-align:center;font-weight:500}
.lede{font-size:11px;color:var(--muted);text-align:center;margin-top:14px}
.how{left:0;top:866px;width:1200px}
.steps{display:flex;justify-content:center;gap:86px;margin-top:56px}
.step{width:264px;text-align:center}
.step .disc{width:122px;height:122px;border-radius:50%;margin:0 auto 20px;display:flex;align-items:center;justify-content:center}
.step h3{font-family:"Montserrat",sans-serif;font-size:13px;color:var(--blue);font-weight:500}
.step h3.alt{color:var(--red)}
.step p{font-size:11px;color:var(--muted);line-height:24px;margin-top:12px}
.why{left:0;top:1262px;width:1200px;height:410px;background:var(--grey-band)}
.boat-photo{left:0;top:98px;width:492px;height:214px;background:linear-gradient(180deg,#eef1f4,#c9ced6 60%,#eef1f4)}
.why-body{left:502px;top:32px;width:590px}
.why-body h2{font-family:"Montserrat",sans-serif;font-size:23px;color:var(--blue);font-weight:500}
.why-body>p{font-size:11px;color:var(--muted);line-height:22px;margin-top:14px}
.point{display:flex;gap:30px;margin-top:24px;font-size:11px;color:var(--muted);line-height:23px;align-items:flex-start}
.point b{flex:none;width:31px;height:31px;border-radius:50%;background:var(--blue);color:var(--white);font-size:10px;font-weight:600;display:flex;align-items:center;justify-content:center;box-shadow:0 0 0 3px #cdd8ea}
.faq{left:0;top:1702px;width:1200px}
.accordion{left:107px;top:1809px;width:462px}
.acc-item{height:49px;border:1px solid #ddd;margin-bottom:8px;display:flex;align-items:center;justify-content:space-between;padding:0 16px 0 18px;font-family:"Roboto Slab",serif;font-size:15px;color:#555}
.acc-item i{width:16px;height:16px;border-radius:50%;background:#555;color:var(--white);font-style:normal;font-size:14px;line-height:16px;text-align:center;font-family:Arial,sans-serif}
.speed-photo{left:643px;top:1793px;width:470px;height:302px;background:linear-gradient(180deg,#9fc4e3 0%,#cfe0ee 30%,#2a74b4 45%,#1a5b9c 100%)}
.footer{left:0;top:2147px;width:1200px;height:312px;background:linear-gradient(180deg,#2a5eb0,#1e4f9e);color:var(--white)}
.fcol{position:absolute;top:30px}
.fcol h4{font-family:"Montserrat",sans-serif;font-size:20px;font-weight:500}
.fcol p{font-size:11px;line-height:24px}
.f-brand{left:85px;width:270px}
.f-brand .mark{width:52px;height:52px;border-radius:50%;background:var(--white);margin:0 0 10px 85px}
.f-brand .name{font-family:"Montserrat",sans-serif;font-size:21px;font-weight:500;text-transform:uppercase;margin-bottom:12px}
.f-contact{left:388px;top:42px}
.f-contact li{list-style:none;font-size:11px;display:flex;gap:14px;margin-top:14px;align-items:flex-start}
.f-contact li span.ic{width:11px;height:11px;flex:none;margin-top:2px}
.f-news{left:647px;top:42px;width:230px}
.email-in{width:230px;height:32px;background:var(--white);color:var(--muted);font-size:11px;padding:0 12px;display:flex;align-items:center;margin-top:14px}
.sub-btn{display:inline-block;margin-top:10px;background:var(--red);font-size:10px;padding:6px 8px;font-family:"Montserrat",sans-serif}
.f-follow{left:903px;top:42px;width:210px}
.socials{display:flex;gap:6px;margin-top:14px}
.socials i{width:36px;height:36px;border:2px solid var(--white);border-radius:50%}
.copyright{left:0;top:2394px;width:1200px;border-top:1px solid rgba(255,255,255,.25);text-align:center;font-size:11px;color:var(--white);padding-top:20px}
</style>
</head>
<body>
<header>
  <div class="abs brand"><span class="brand-mark"></span><span class="brand-name">Pellham Grove Trust</span></div>
  <div class="abs tollfree">
    <span class="ring"><svg width="22" height="22" viewBox="0 0 24 24"><path d="M6.6 10.8a15 15 0 006.6 6.6l2.2-2.2c.3-.3.7-.4 1-.2 1.1.4 2.3.6 3.6.6.6 0 1 .4 1 1V20c0 .6-.4 1-1 1A17 17 0 013 4c0-.6.4-1 1-1h3.5c.6 0 1 .4 1 1 0 1.3.2 2.5.6 3.6.1.3 0 .7-.2 1z" fill="none" stroke="#1a4fa0" stroke-width="1.6"/></svg></span>
    <div><small>Call toll-free</small><strong>(000)-482-7350</strong></div>
  </div>
</header>
<nav class="abs nav"><ul><li>HOME</li><li>ABOUT US</li><li>SERVICES</li><li>HOW IT WORKS</li><li>CHARITIES</li><li>CONTACT US</li></ul></nav>
<div class="abs donate-tab">DONATE HERE</div>

<section class="abs hero" role="img" aria-label="Photo of a child hugging a soldier holding a small American flag, with a flag in the background"></section>
<form class="abs donate-form">
  <div class="row"><div class="field">First Name :</div><div class="field">Last Phone :</div></div>
  <div class="row"><div class="field">Email :</div><div class="field">Phone :</div></div>
  <div class="field">Address :</div>
  <div class="field">City :</div>
  <div class="field">State :<span>▾</span></div>
  <div class="field">Zip Code :</div>
  <div class="row"><div class="field">Year :<span>▾</span></div><div class="field">Model :<span>▾</span></div></div>
  <div class="btn-donate">DONATE NOW!</div>
</form>
<div class="abs dots"><i></i><i></i><i></i><i></i></div>

<section class="abs benefits">
  <div class="benefit"><svg width="72" height="72" viewBox="0 0 72 72"><circle cx="36" cy="36" r="32" fill="none" stroke="#fff" stroke-width="5"/><text x="36" y="48" text-anchor="middle" font-size="36" font-family="Arial" font-weight="700" fill="#fff">$</text><line x1="14" y1="14" x2="58" y2="58" stroke="#fff" stroke-width="5"/></svg>You have no costs</div>
  <div class="benefit"><svg width="96" height="72" viewBox="0 0 96 72"><rect x="8" y="38" width="52" height="18" fill="#fff"/><path d="M60 56V30h16l10 14v12z" fill="#fff"/><line x1="30" y1="38" x2="48" y2="12" stroke="#fff" stroke-width="4"/><circle cx="24" cy="60" r="7" fill="#c21a1a" stroke="#fff" stroke-width="3"/><circle cx="74" cy="60" r="7" fill="#c21a1a" stroke="#fff" stroke-width="3"/></svg>Free towing,<br>running or not</div>
  <div class="benefit"><svg width="72" height="72" viewBox="0 0 72 72"><rect x="16" y="6" width="40" height="56" fill="none" stroke="#fff" stroke-width="3"/><text x="30" y="42" text-anchor="middle" font-size="20" font-family="Arial" fill="#fff">$</text><line x1="38" y1="28" x2="50" y2="28" stroke="#fff" stroke-width="3"/><line x1="38" y1="38" x2="50" y2="38" stroke="#fff" stroke-width="3"/><line x1="22" y1="50" x2="50" y2="50" stroke="#fff" stroke-width="3"/></svg>We issue you an<br>IRS tax receipt</div>
  <div class="benefit"><svg width="72" height="72" viewBox="0 0 72 72"><rect x="24" y="6" width="36" height="50" fill="none" stroke="#fff" stroke-width="3"/><circle cx="30" cy="38" r="14" fill="#c21a1a" stroke="#fff" stroke-width="3"/><line x1="20" y1="48" x2="8" y2="62" stroke="#fff" stroke-width="5"/><text x="30" y="45" text-anchor="middle" font-size="18" font-family="Arial" font-weight="700" fill="#fff">!</text></svg>We take care of<br>all paperwork</div>
  <div class="benefit"><svg width="72" height="72" viewBox="0 0 72 72"><path d="M36 6v40H14z" fill="none" stroke="#fff" stroke-width="3"/><path d="M40 12l20 34H40z" fill="#fff"/><path d="M10 50h52l-8 8H18z" fill="#fff"/><path d="M6 64q8-5 15 0t15 0 15 0 15 0" fill="none" stroke="#fff" stroke-width="3"/></svg>We take care of<br>DMV &amp; Smog issues</div>
</section>

<section class="abs how">
  <h2 class="section-title">HOW TO DONATE</h2>
  <p class="lede">Sed ut perspiciatis unde omnis iste natus error sit voluptatem accusantium doloremque laudantium,</p>
  <div class="steps">
    <div class="step"><div class="disc" style="background:var(--blue)"><svg width="60" height="54" viewBox="0 0 60 54"><rect x="4" y="4" width="52" height="36" fill="none" stroke="#fff" stroke-width="3"/><rect x="12" y="12" width="12" height="12" fill="#fff"/><line x1="30" y1="15" x2="48" y2="15" stroke="#fff" stroke-width="3"/><line x1="30" y1="23" x2="48" y2="23" stroke="#fff" stroke-width="3"/><line x1="12" y1="31" x2="48" y2="31" stroke="#fff" stroke-width="3"/><path d="M22 40l-4 10h24l-4-10" fill="#fff"/></svg></div><h3>FILL OUT THE ONLINE FORM</h3><p>Sed ut perspiciatis unde omnis iste natus error sit voluptatem accusantium doloremque laudantium, beatae vitae dicta sunt explicabo.</p></div>
    <div class="step"><div class="disc" style="background:var(--red)"><svg width="60" height="56" viewBox="0 0 60 56"><path d="M30 4v30H12z" fill="#fff"/><path d="M34 8l16 26H34z" fill="#fff"/><path d="M6 38h48l-7 7H13z" fill="#fff"/><path d="M4 52q6-4 13 0t13 0 13 0 13 0" fill="none" stroke="#fff" stroke-width="3"/></svg></div><h3 class="alt">WE TOW YOUR BOAT</h3><p>Sed ut perspiciatis unde omnis iste natus error sit voluptatem accusantium doloremque laudantium, beatae vitae dicta sunt explicabo.</p></div>
    <div class="step"><div class="disc" style="background:var(--blue)"><svg width="60" height="60" viewBox="0 0 60 60"><rect x="8" y="6" width="30" height="42" fill="none" stroke="#fff" stroke-width="3"/><rect x="30" y="26" width="22" height="30" fill="#fff"/><rect x="34" y="30" width="14" height="6" fill="#1a4fa0"/><g fill="#1a4fa0"><rect x="34" y="40" width="4" height="4"/><rect x="40" y="40" width="4" height="4"/><rect x="46" y="40" width="2" height="4"/><rect x="34" y="47" width="4" height="4"/><rect x="40" y="47" width="4" height="4"/></g><line x1="14" y1="16" x2="30" y2="16" stroke="#fff" stroke-width="3"/><line x1="14" y1="24" x2="26" y2="24" stroke="#fff" stroke-width="3"/></svg></div><h3>TAX WRITE-OFF</h3><p>Sed ut perspiciatis unde omnis iste natus error sit voluptatem accusantium doloremque laudantium, beatae vitae dicta sunt explicabo.</p></div>
  </div>
</section>

<section class="abs why">
  <div class="abs boat-photo" role="img" aria-label="Photo of a white motor yacht"></div>
  <div class="abs why-body">
    <h2>WHY DONATE YOUR BOAT TO US</h2>
    <p>Sed ut perspiciatis unde omnis iste natus error sit voluptatem accusantium doloremque laudantium, totam rem inventore veritatis et quasi architecto beatae vitae dicta sunt explicabo.</p>
    <div class="point"><b>01</b><span>Sed ut perspiciatis unde omnis iste natus error sit voluptatem</span></div>
    <div class="point"><b>02</b><span>Sed ut perspiciatis unde omnis iste natus error sit voluptatem accusantium doloremque veritatis et quasi architecto beatae vitae dicta</span></div>
    <div class="point"><b>03</b><span>Sed ut perspiciatis unde omnis iste natus error sit voluptatem</span></div>
    <div class="point"><b>04</b><span>Sed ut perspiciatis unde omnis iste natus error sit voluptatem accusantium doloremque veritatis et quasi architecto beatae vitae dicta</span></div>
  </div>
</section>

<section class="abs faq">
  <h2 class="section-title">FREQUENTLY ASKED QUESTIONS</h2>
  <p class="lede">Sed ut perspiciatis unde omnis iste natus error sit voluptatem accusantium doloremque laudantium,</p>
</section>
<div class="abs accordion">
  <div class="acc-item">Aspernatur aut odit aut fugit<i>+</i></div>
  <div class="acc-item">But I must explain to you how all this mistaken<i>+</i></div>
  <div class="acc-item">Expound the actual teachings of the great<i>+</i></div>
  <div class="acc-item">Sed ut perspiciatis unde omnis iste natus error<i>+</i></div>
  <div class="acc-item">Sed ut perspiciatis unde omnis iste natus error<i>+</i></div>
</div>
<div class="abs speed-photo" role="img" aria-label="Photo of a speedboat cruising on blue sea"></div>

<footer class="abs footer">
  <div class="fcol f-brand">
    <div class="mark"></div>
    <div class="name">Pellham Grove Trust</div>
    <p>Sed ut perspiciatis unde omnis iste natus error sit voluptatem accusantium doloremque laudantium, totam beatae vitae dicta sunt explicabo.</p>
  </div>
  <div class="fcol f-contact">
    <h4>CONTACT US</h4>
    <ul>
      <li><span class="ic" style="background:#fff;border-radius:2px"></span>(000)-482-7350 &nbsp;(Phone)</li>
      <li><span class="ic" style="background:#fff;border-radius:50%"></span>(000)-482-7351 &nbsp;(Fax)</li>
      <li><span class="ic" style="border:1.5px solid #fff"></span><u>info@pellhamgrove.org</u></li>
      <li><span class="ic"><svg width="11" height="13" viewBox="0 0 11 13"><path d="M5.5 0a4.5 4.5 0 014.5 4.5C10 8 5.5 13 5.5 13S1 8 1 4.5A4.5 4.5 0 015.5 0z" fill="#fff"/></svg></span><span># 2564 Lorem Ipsum Dummy<br>Lorem Ipsum Dummy</span></li>
    </ul>
  </div>
  <div class="fcol f-news">
    <h4>NEWSLETTER</h4>
    <p style="margin-top:14px;line-height:20px">Register Your email address to get information ablout us</p>
    <div class="email-in">Email Address</div>
    <span class="sub-btn">SUBSCRIBE</span>
  </div>
  <div class="fcol f-follow">
    <h4>FOLLOW US</h4>
    <p style="margin-top:14px;line-height:20px">Lorem ipsum dolor sit amet, conse ctetur adipiscing elit. Nulla in purus nibh. Donec ornare</p>
    <div class="socials"><i></i><i></i><i></i><i></i><i></i></div>
  </div>
</footer>
<div class="abs copyright">© Copyright 2017 Pellham Grove Trust All Rights Reserved</div>
</body>
</html>
```